Fenwick Ridge Accounting - New client package

I need a stationary package (presentation folder cover, welcome letter template/design, sample financial report template/design, business card and new logo) for my accounting business. I would like to see designs that use the color blue. Financial icons can be included in the design. The final design should be clean and communicate professionalism and the use of modern; user-friendly technology. Attached postcard files should help with overall design concept.

```html
<!DOCTYPE html>
<html lang="en">
<head>
<meta charset="utf-8">
<title>Fenwick Ridge Accounting – Business Card</title>
<link rel="stylesheet" href="https://fonts.googleapis.com/css2?family=Roboto:wght@400;500&family=Roboto+Condensed:wght@500&display=swap">
<style>
  :root {
    --stage: #181818;
    --brand-blue: #2d5b8a;
    --brand-blue-soft: #38668f;
    --band-blue: #306698;
    --paper: #f7f8f9;
    --ink: #3a3d40;
    --charcoal: #3f4347;
    --white: #ffffff;
  }
  * { margin: 0; padding: 0; box-sizing: border-box; }
  html, body { width: 1200px; height: 1200px; overflow: hidden; }
  body {
    background: var(--stage);
    font-family: "Roboto", Arial, sans-serif;
    position: relative;
  }
  .card {
    position: absolute;
    left: 319px;
    width: 561px;
    height: 339px;
    overflow: hidden;
  }
  .card--front { top: 251px; background: var(--brand-blue); }
  .card--back  { top: 609px; background: var(--paper); color: var(--ink); }

  .front-disc {
    position: absolute;
    left: 105px; top: -3px;
    width: 344px; height: 344px;
    border-radius: 50%;
    background: var(--brand-blue-soft);
  }
  .front-name {
    position: absolute;
    left: 0; right: 0; top: 125px;
    text-align: center;
    color: var(--white);
    font-weight: 500;
    text-transform: uppercase;
  }
  .front-name .line-main { display: block; font-size: 52px; letter-spacing: 0.5px; line-height: 54px; }
  .front-name .line-sub  { display: block; font-size: 25px; letter-spacing: 24px; line-height: 32px; padding-left: 24px; margin-top: 2px; }

  .back-mark {
    position: absolute;
    left: 26px; top: 54px;
    width: 92px; height: 92px;
    border-radius: 50%;
    background: var(--brand-blue);
  }
  .back-name {
    position: absolute;
    left: 147px; top: 68px;
    font-weight: 500;
    text-transform: uppercase;
  }
  .back-name .line-main { display: block; font-size: 43px; letter-spacing: 0.3px; line-height: 44px; color: var(--brand-blue); }
  .back-name .line-sub  { display: block; font-size: 21px; letter-spacing: 19px; line-height: 28px; padding-left: 8px; margin-top: 2px; color: var(--ink); }

  .person { position: absolute; left: 26px; top: 188px; }
  .person-name {
    font-family: "Roboto Condensed", "Arial Narrow", sans-serif;
    font-weight: 500;
    font-size: 23px;
    color: var(--brand-blue);
    line-height: 26px;
  }
  .person-role { font-size: 14px; line-height: 20px; margin-top: 2px; }
  .address {
    position: absolute; left: 26px; top: 264px;
    font-size: 14px; line-height: 21px; font-style: normal;
  }
  .contacts {
    position: absolute; left: 296px; top: 206px;
    list-style: none; font-size: 14px; line-height: 21.5px;
  }
  .contacts li { display: flex; align-items: center; }
  .contacts svg { width: 13px; height: 13px; margin-right: 13px; fill: var(--brand-blue); }
  .base-strip {
    position: absolute; left: 0; bottom: 0;
    width: 240px; height: 13px;
    background: var(--charcoal);
  }
  .tagline-band { position: absolute; left: 0; top: 0; }
  .tagline {
    position: absolute; left: 295px; top: 308px;
    color: var(--white); font-size: 14.5px; letter-spacing: 0.2px;
    text-transform: uppercase;
  }
</style>
</head>
<body>
  <section class="card card--front">
    <div class="front-disc"></div>
    <h1 class="front-name">
      <span class="line-main">Fenwick Ridge</span>
      <span class="line-sub">Accounting</span>
    </h1>
  </section>

  <section class="card card--back">
    <div class="back-mark"></div>
    <h2 class="back-name">
      <span class="line-main">Fenwick Ridge</span>
      <span class="line-sub">Accounting</span>
    </h2>

    <div class="person">
      <p class="person-name">Clara Whitfield</p>
      <p class="person-role">Managing Director</p>
    </div>
    <address class="address">58 Harbor Lane, Millbrook,<br>Easton, US 204518</address>

    <ul class="contacts">
      <li>
        <svg viewBox="0 0 16 16" aria-hidden="true"><path d="M1 5c0-2 3-3 7-3s7 1 7 3v1h-3V5H4v1H1zM4 7h8l2 7H2zm4 2a2 2 0 100 4 2 2 0 000-4z"/></svg>
        1.877.555.0142
      </li>
      <li>
        <svg viewBox="0 0 16 16" aria-hidden="true"><path d="M1 3h14v10H1zm1.5 1.2L8 8.6l5.5-4.4zM2 5.4V12h12V5.4L8 10.2z"/></svg>
        info@fenwickridgeacct.com
      </li>
      <li>
        <svg viewBox="0 0 16 16" aria-hidden="true"><path d="M8 1a7 7 0 100 14A7 7 0 008 1zm0 1.3c.8.8 1.4 2 1.6 3.4H6.4C6.6 4.3 7.2 3.1 8 2.3zM2.4 7h2.7v2H2.4zm4 0h3.2v2H6.4zm4.5 0h2.7v2h-2.7zM6.4 10.3h3.2c-.2 1.4-.8 2.6-1.6 3.4-.8-.8-1.4-2-1.6-3.4z"/></svg>
        www.fenwickridgeacct.com
      </li>
    </ul>

    <div class="base-strip"></div>
    <svg class="tagline-band" width="561" height="339" viewBox="0 0 561 339" aria-hidden="true">
      <path d="M225 339 L249 303 Q253 297 261 297 L561 297 L561 339 Z" fill="var(--band-blue)"/>
    </svg>
    <p class="tagline">Boutique Accounting Firm</p>
  </section>
</body>
</html>
```